Expedition Cruise Sales Website for the Polar Regions (Antarctica & Arctic)

This will be a website for selling cruises.
This site should have a homepage, a ship page, destinations, and itineraries.
I have created a file specifying each page, and it is attached.
Pages:
1. Home
2. Cruise Lines
- 2.1 Ships
3. Destinations
- 3.1 Region - 3.2 Country - 3.3 City
4. Itineraries
- 4.1 Itinerary
5. Blog / Travel Tips 6. About Us
7. Contact
Please take a look on the attached pdf
Target Market(s)
Expedition Travelers
Coding
Coded - Design and coding required
Number of Pages Required
5+ page
Font styles to use
Look and feel
Each slider illustrates characteristics of the customer's brand and the style your logo design should communicate.

```html
<!DOCTYPE html>
<html lang="en">
<head>
<meta charset="utf-8">
<title>Polarvia – Expedition Cruises</title>
<link rel="stylesheet" href="https://fonts.googleapis.com/css2?family=Poppins:wght@500;600;700&family=Roboto:wght@400;500;700&display=swap">
<style>
:root{
  --navy:#0f1a36;
  --blue:#2a5ea8;
  --blue-dark:#1e4f99;
  --blue-soft:#dbe6f4;
  --ice:#eef4fb;
  --ink:#1b1b1b;
  --muted:#444;
  --white:#fff;
  --star:#f0a030;
}
*{box-sizing:border-box;margin:0;padding:0}
html,body{width:1200px;height:4535px;overflow:hidden}
body{position:relative;font-family:"Roboto",sans-serif;color:var(--ink);background:var(--white)}
.abs{position:absolute}
h2.section-title{position:absolute;left:0;width:1200px;text-align:center;font-family:"Poppins",sans-serif;font-weight:600;font-size:40px;color:var(--ink)}
.title-bar{position:absolute;left:564px;width:72px;height:4px;background:var(--blue);border-radius:2px}

/* top bar */
.topbar{top:0;left:0;width:1200px;height:46px;background:var(--navy);color:#fff;font-size:12px}
.topbar .mail{left:110px;top:16px}
.topbar .mail u{color:#fff}
.topbar .call{left:722px;top:16px}
.social{display:flex;gap:0}
.social span{width:38px;height:46px;border-left:1px solid #2a3556;display:block;position:relative}
.social span::after{content:"";position:absolute;left:13px;top:17px;width:12px;height:12px;border:2px solid #fff;border-radius:3px}
.social span.on{background:var(--blue)}

/* header */
.header{top:46px;left:0;width:1200px;height:84px;background:#fff;z-index:3}
.logo-disc{left:88px;top:20px;width:194px;height:194px;border-radius:50%;background:#fff;z-index:3}
.logo{left:110px;top:64px;z-index:4;text-align:center;width:148px}
.logo i{display:block;width:38px;height:38px;border-radius:50%;background:var(--blue);margin:0 auto 6px}
.logo b{font-family:"Poppins",sans-serif;font-weight:600;font-size:27px;color:var(--blue)}
.nav{left:330px;top:74px;display:flex;gap:34px;font-size:15px;font-weight:500;z-index:4}
.nav a{color:var(--ink);text-decoration:none}
.nav a.cur{background:var(--blue-soft);color:var(--blue);padding:6px 16px;margin:-6px -10px;border-radius:16px}

/* hero */
.hero{top:130px;left:0;width:1200px;height:600px;background:linear-gradient(160deg,#6e8da3 0%,#2f6f8c 35%,#1d5c80 60%,#164a6e 100%)}
.hero h1{position:absolute;top:150px;left:0;width:1200px;text-align:center;font-family:"Poppins",sans-serif;font-weight:600;font-size:44px;line-height:54px;color:#fff}
.hero p{position:absolute;top:272px;left:0;width:1200px;text-align:center;font-size:19px;font-weight:500;line-height:29px;color:#fff}
.field{position:absolute;top:345px;height:46px;width:248px;background:#fff;border-radius:23px;font-size:13px;color:#555;padding:14px 0 0 36px}
.field svg{position:absolute;left:18px;top:16px}
.book{position:absolute;top:345px;left:732px;width:248px;height:46px;background:var(--blue);border-radius:23px;color:#fff;font-weight:700;font-size:14px;text-align:center;line-height:46px}

/* cruise cards */
.card{position:absolute;background:#fff;border-radius:18px;box-shadow:0 6px 18px rgba(0,0,0,.13)}
.cruise .photo{position:absolute;left:7px;top:7px;right:7px;height:225px;border-radius:14px}
.cruise .price{position:absolute;top:250px;width:100%;text-align:center;color:var(--blue);font-weight:700;font-size:20px}
.cruise h3,.line h3{position:absolute;width:100%;text-align:center;font-weight:700;font-size:17px}
.cruise h3{top:282px}
.cruise p{position:absolute;top:314px;left:22px;right:22px;text-align:center;font-size:13px;line-height:21px;color:var(--muted)}
.plan{position:absolute;top:414px;left:74px;width:160px;height:44px;border-radius:22px;background:var(--blue-soft);color:var(--blue);font-weight:700;font-size:14px;text-align:center;line-height:44px}
.plan.on{background:var(--blue);color:#fff}

/* destinations */
.dest-bg{top:1450px;left:0;width:1200px;height:870px}
.dest .photo{position:absolute;left:7px;top:7px;right:7px;height:327px;border-radius:14px}
.pin{position:absolute;top:310px;left:50%;margin-left:-31px;width:62px;height:62px;border-radius:50%;background:#fff;display:flex;align-items:center;justify-content:center}
.pin i{width:48px;height:48px;border-radius:50%;background:var(--blue);display:flex;align-items:center;justify-content:center}
.dest h3{position:absolute;top:390px;width:100%;text-align:center;font-size:16px;font-weight:700}
.dest h3 span{font-weight:500;font-size:14px}
.dest p{position:absolute;top:420px;left:40px;right:40px;text-align:center;font-size:13px;line-height:22px;color:var(--muted)}
.dots{top:2239px;left:572px;display:flex;gap:10px}
.dots i{width:12px;height:12px;border-radius:50%;background:#aab4c2}
.dots i.on{background:var(--blue)}

/* cruise lines */
.line{border-top:5px solid var(--blue);border-radius:6px}
.line h3{top:78px}
.line .stars{position:absolute;top:108px;width:100%;text-align:center;color:var(--star);font-size:13px;letter-spacing:1px}
.line p{position:absolute;top:136px;left:24px;right:24px;text-align:center;font-size:15px;line-height:24px;color:var(--muted)}
.badge{position:absolute;top:-52px;left:50%;margin-left:-47px;width:94px;height:94px;border-radius:50%;background:#fff;border:5px solid var(--blue)}
.badge i{position:absolute;left:22px;top:22px;width:40px;height:40px;border-radius:50%;background:var(--blue-soft)}
.round{position:absolute;width:36px;height:36px;border-radius:50%;display:flex;align-items:center;justify-content:center}

/* testimonials */
.testi-bg{top:2940px;left:0;width:1200px;height:550px}
.quote{position:absolute;background:#fff;border-radius:28px;width:408px;height:230px;top:3175px}
.quote .mark{position:absolute;left:80px;top:22px}
.quote p{position:absolute;left:80px;right:26px;top:68px;font-size:13.5px;line-height:21px;color:#333}
.quote b{position:absolute;left:80px;top:180px;font-family:"Poppins",sans-serif;font-size:15px;font-weight:600}
.quote .stars{position:absolute;left:80px;top:202px;color:var(--star);font-size:11px}
.avatar{position:absolute;top:3233px;width:110px;height:110px;border-radius:50%;border:4px solid #fff;background:linear-gradient(160deg,#c9b8a6,#7a6a5c)}

/* contact */
.contact h2{position:absolute;top:3578px;left:579px;font-family:"Poppins",sans-serif;font-weight:600;font-size:38px}
.contact .bar{position:absolute;top:3628px;left:579px;width:72px;height:4px;background:var(--blue)}
.label{position:absolute;font-size:14px;font-weight:500}
.input{position:absolute;height:40px;width:252px;border:1px solid #d6d6d6;box-shadow:0 2px 5px rgba(0,0,0,.08);font-size:12.5px;color:#555;padding:12px 0 0 18px}
.send{position:absolute;left:924px;top:3975px;width:164px;height:42px;border-radius:21px;background:var(--blue);color:#fff;font-weight:700;font-size:13px;text-align:center;line-height:42px}

/* footer */
.footer{top:4110px;left:0;width:1200px;height:425px}
.f-logo{left:110px;top:4290px;width:230px;text-align:center;color:#fff}
.f-logo i{display:block;width:62px;height:62px;border-radius:50%;background:#fff;margin:0 auto 10px}
.f-logo b{font-family:"Poppins",sans-serif;font-weight:600;font-size:40px}
.f-col{color:#fff}
.f-col h4{font-family:"Poppins",sans-serif;font-weight:600;font-size:16px;margin-bottom:14px}
.f-col li{list-style:none;font-size:14px;height:34px;display:flex;align-items:center;gap:18px}
.f-col li::before{content:"";width:12px;height:12px;border-radius:50%;background:var(--blue)}
.news-line{left:776px;top:4282px;width:284px;border-bottom:1px solid #fff;color:#fff;font-size:13px;padding-bottom:10px}
.subscribe{left:776px;top:4311px;width:130px;height:44px;border-radius:22px;background:var(--blue);color:#fff;font-weight:700;font-size:14px;text-align:center;line-height:44px}
.f-rule{left:110px;top:4470px;width:978px;height:1px;background:#33406a}
.copy{left:0;top:4498px;width:1200px;text-align:center;color:#fff;font-size:13px}
.f-social{left:930px;top:4486px;display:flex;gap:8px}
.f-social i{width:34px;height:34px;border-radius:50%;background:#2b3658;display:block}
.f-social i:first-child{background:var(--blue)}
.chat{left:1120px;top:4412px;width:42px;height:42px;border-radius:50%;background:#fff;border:3px solid var(--navy);box-shadow:0 0 0 2px #fff}
</style>
</head>
<body>

<!-- top bar -->
<div class="abs topbar">
  <div class="abs mail">✉ Email Us: <u>info@polarvia.com</u></div>
  <div class="abs call">☏ Call Us: +1 (555) 014 2290</div>
  <div class="abs social" style="left:937px;top:0"><span class="on"></span><span></span><span></span><span></span></div>
</div>

<!-- header -->
<div class="abs header"></div>
<div class="abs logo-disc"></div>
<div class="abs logo"><i></i><b>Polarvia</b></div>
<nav class="abs nav">
  <a class="cur">Home</a><a>Cruise Lines</a><a>Destinations</a><a>Itineraries</a><a>Blog/Travel Tips</a><a>About Us</a><a>Contact</a>
</nav>

<!-- hero -->
<section class="abs hero" role="img" aria-label="Coastal town on cliffs above a turquoise bay with a cruise ship at sea">
  <h1>Discover New Horizons,<br>Cruise in Style</h1>
  <p>Lorem ipsum dolor sit amet, consectetur adipiscing elit, sed do<br>eiusmod incididunt ut laborea.</p>
  <div class="field" style="left:220px"><svg width="10" height="14" viewBox="0 0 10 14"><path d="M5 0a5 5 0 0 0-5 5c0 4 5 9 5 9s5-5 5-9a5 5 0 0 0-5-5z" fill="#666"/><circle cx="5" cy="5" r="2" fill="#fff"/></svg>Location</div>
  <div class="field" style="left:476px"><svg width="12" height="12" viewBox="0 0 12 12"><rect x="0.5" y="1.5" width="11" height="10" rx="1" fill="none" stroke="#666"/><path d="M0.5 4.5h11" stroke="#666"/></svg>Date</div>
  <div class="book">BOOK NOW</div>
</section>
<svg class="abs" style="left:0;top:620px" width="1200" height="112" viewBox="0 0 1200 112"><path d="M0 80 C120 20 200 130 330 90 C460 50 520 -10 650 40 C780 90 880 10 1010 30 C1100 45 1160 20 1200 5 L1200 112 L0 112 Z" fill="#fff"/></svg>

<!-- best cruises -->
<h2 class="section-title" style="top:798px">Best Antarctic Cruises</h2>
<div class="title-bar" style="top:853px"></div>
<svg class="abs" style="left:38px;top:1130px" width="40" height="24" viewBox="0 0 40 24"><path d="M38 12H3M13 2L3 12l10 10" fill="none" stroke="#555" stroke-width="2"/></svg>
<svg class="abs" style="left:1122px;top:1130px" width="40" height="24" viewBox="0 0 40 24"><path d="M2 12h35M27 2l10 10-10 10" fill="none" stroke="#555" stroke-width="2"/></svg>

<div class="card cruise" style="left:111px;top:898px;width:309px;height:488px">
  <div class="photo" role="img" aria-label="Motor yacht speeding across the sea at sunset" style="background:linear-gradient(180deg,#e8a24a,#3a6f9e 60%,#12385e)"></div>
  <div class="price">$29,999.99</div><h3>LOREM IPSUM DOLOR</h3>
  <p>Sed ut perspiciatis unde omnis iste natus error sit voluptatem accusantium doloremque laudantium, totam rem aperiam, eaque ipsa.</p>
  <div class="plan">SELECT PLAN</div>
</div>
<div class="card cruise" style="left:445px;top:898px;width:309px;height:488px">
  <div class="photo" role="img" aria-label="Large cruise ship among icebergs" style="background:linear-gradient(180deg,#5a7ea6,#c7d7e6 55%,#3f5f80)"></div>
  <div class="price">$29,999.99</div><h3>LOREM IPSUM DOLOR</h3>
  <p>Sed ut perspiciatis unde omnis iste natus error sit voluptatem accusantium doloremque laudantium, totam rem aperiam, eaque ipsa.</p>
  <div class="plan on">SELECT PLAN</div>
</div>
<div class="card cruise" style="left:779px;top:898px;width:309px;height:488px">
  <div class="photo" role="img" aria-label="Cruise ship on calm water under a golden sunset" style="background:linear-gradient(180deg,#3c6a9a,#e0a058 50%,#1f4f7a)"></div>
  <div class="price">$29,999.99</div><h3>LOREM IPSUM DOLOR</h3>
  <p>Sed ut perspiciatis unde omnis iste natus error sit voluptatem accusantium doloremque laudantium, totam rem aperiam, eaque ipsa.</p>
  <div class="plan">SELECT PLAN</div>
</div>

<!-- destinations -->
<svg class="abs dest-bg" width="1200" height="870" viewBox="0 0 1200 870">
  <path d="M0 120 C250 -20 800 -40 1200 130 L1200 870 L0 870 Z" fill="#eef4fb"/>
  <path d="M0 150 C220 -10 820 -50 1200 290" fill="none" stroke="#2a5ea8" stroke-width="16"/>
</svg>
<h2 class="section-title" style="top:1595px">Our Destinations</h2>
<div class="title-bar" style="top:1650px"></div>
<div class="card dest" style="left:111px;top:1700px;width:475px;height:488px">
  <div class="photo" role="img" aria-label="Penguins on snow in front of a cruise ship" style="background:linear-gradient(180deg,#b9c4ce,#e7ecf1 70%,#ffffff)"></div>
  <div class="pin"><i><svg width="14" height="18" viewBox="0 0 10 14"><path d="M5 0a5 5 0 0 0-5 5c0 4 5 9 5 9s5-5 5-9a5 5 0 0 0-5-5z" fill="#fff"/><circle cx="5" cy="5" r="2" fill="#2a5ea8"/></svg></i></div>
  <h3>ANTARCTICA, <span>Lorem Ipsum</span></h3>
  <p>Sed ut perspiciatis unde omnis iste natus error sit voluptatem accusantium doloremque laudea.</p>
</div>
<div class="card dest" style="left:614px;top:1700px;width:474px;height:488px">
  <div class="photo" role="img" aria-label="Snowy mountains reflected in icy water" style="background:linear-gradient(180deg,#2f5f8e,#9fb9cf 50%,#1f4a72)"></div>
  <div class="pin"><i><svg width="14" height="18" viewBox="0 0 10 14"><path d="M5 0a5 5 0 0 0-5 5c0 4 5 9 5 9s5-5 5-9a5 5 0 0 0-5-5z" fill="#fff"/><circle cx="5" cy="5" r="2" fill="#2a5ea8"/></svg></i></div>
  <h3>ANTARCTICA, <span>Lorem Ipsum</span></h3>
  <p>Sed ut perspiciatis unde omnis iste natus error sit voluptatem accusantium doloremque laudea.</p>
</div>
<div class="abs dots"><i></i><i class="on"></i><i></i></div>

<!-- cruise lines -->
<h2 class="section-title" style="top:2407px">Cruise Lines</h2>
<div class="title-bar" style="top:2461px"></div>
<div class="round" style="left:43px;top:2686px;background:#e3e6ea"><svg width="10" height="14" viewBox="0 0 10 14"><path d="M8 1L2 7l6 6" fill="none" stroke="#222" stroke-width="2"/></svg></div>
<div class="round" style="left:1121px;top:2686px;background:var(--blue)"><svg width="10" height="14" viewBox="0 0 10 14"><path d="M2 1l6 6-6 6" fill="none" stroke="#fff" stroke-width="2"/></svg></div>
<div class="card line" style="left:111px;top:2548px;width:305px;height:308px">
  <div class="badge"><i></i></div><h3>LOREM IPSUM DOLOR</h3><div class="stars">★★★★★</div>
  <p>Lorem ipsum dolor sit amet, cons ectetur adipiscing elit, sed do eiusmod tempor incididunt ut labore et dolore magna aliqua. Ut enim ad minim veniam, quis nostrud ullamco laboris nisiea.</p>
</div>
<div class="card line" style="left:447px;top:2548px;width:305px;height:308px">
  <div class="badge"><i></i></div><h3>LOREM IPSUM DOLOR</h3><div class="stars">★★★★★</div>
  <p>Lorem ipsum dolor sit amet, cons ectetur adipiscing elit, sed do eiusmod tempor incididunt ut labore et dolore magna aliqua. Ut enim ad minim veniam, quis nostrud ullamco laboris nisiea.</p>
</div>
<div class="card line" style="left:783px;top:2548px;width:305px;height:308px">
  <div class="badge"><i></i></div><h3>LOREM IPSUM DOLOR</h3><div class="stars">★★★★★</div>
  <p>Lorem ipsum dolor sit amet, cons ectetur adipiscing elit, sed do eiusmod tempor incididunt ut labore et dolore magna aliqua. Ut enim ad minim veniam, quis nostrud ullamco laboris nisiea.</p>
</div>

<!-- testimonials -->
<svg class="abs testi-bg" width="1200" height="550" viewBox="0 0 1200 550" role="img" aria-label="Blue-tinted coastal mountain landscape">
  <defs><linearGradient id="tb" x1="0" y1="0" x2="0" y2="1"><stop offset="0" stop-color="#3a6fb6"/><stop offset="1" stop-color="#2456a0"/></linearGradient></defs>
  <path d="M0 20 C80 -10 150 60 260 30 C380 0 430 40 560 20 C680 0 720 -10 820 30 C920 70 1000 0 1100 20 C1150 30 1180 25 1200 20 L1200 550 L0 550 Z" fill="url(#tb)"/>
</svg>
<h2 class="section-title" style="top:3078px;color:#fff">Testimonials</h2>
<div class="title-bar" style="top:3133px;background:#fff"></div>
<svg class="abs" style="left:38px;top:3276px" width="40" height="24" viewBox="0 0 40 24"><path d="M38 12H3M13 2L3 12l10 10" fill="none" stroke="#fff" stroke-width="2"/></svg>
<svg class="abs" style="left:1122px;top:3276px" width="40" height="24" viewBox="0 0 40 24"><path d="M2 12h35M27 2l10 10-10 10" fill="none" stroke="#fff" stroke-width="2"/></svg>
<div class="quote" style="left:181px">
  <svg class="mark" width="36" height="28" viewBox="0 0 36 28"><path d="M0 28V14C0 5 5 0 14 0v6c-4 0-6 3-6 8h6v14zM20 28V14c0-9 5-14 14-14v6c-4 0-6 3-6 8h6v14z" fill="#2a5ea8"/></svg>
  <p>Lorem ipsum dolor sit amet, cons ectetur adip elit, sed do eiusmod tempor incididun ut labor et dolore magna aliqua. Ut enim ad minim veni quis nostrud ullamco laboris nisiea ut aliquip ex ea commodo consequat.</p>
  <b>- MARK ELLISON</b><div class="stars">★★★★★</div>
</div>
<div class="avatar" role="img" aria-label="Portrait of a smiling male customer" style="left:130px"></div>
<div class="quote" style="left:665px">
  <svg class="mark" width="36" height="28" viewBox="0 0 36 28"><path d="M0 28V14C0 5 5 0 14 0v6c-4 0-6 3-6 8h6v14zM20 28V14c0-9 5-14 14-14v6c-4 0-6 3-6 8h6v14z" fill="#2a5ea8"/></svg>
  <p>Lorem ipsum dolor sit amet, cons ectetur adip elit, sed do eiusmod tempor incididun ut labor et dolore magna aliqua. Ut enim ad minim veni quis nostrud ullamco laboris nisiea ut aliquip ex ea commodo consequat.</p>
  <b>- DANIELA</b><div class="stars">★★★★★</div>
</div>
<div class="avatar" role="img" aria-label="Portrait of a smiling female customer" style="left:614px;background:linear-gradient(160deg,#8a6a4e,#2f4a3a)"></div>

<!-- contact -->
<div class="abs" role="img" aria-label="Polar bear and penguin silhouette filled with a cruise ship scene, with sparkles" style="left:110px;top:3620px;width:425px;height:365px;background:linear-gradient(170deg,#3f7fd0,#1a47a0 60%,#0f2f80);border-radius:46% 40% 6% 6%"></div>
<div class="contact">
  <h2>Contact Us</h2><div class="bar"></div>
  <div class="label" style="left:579px;top:3666px">First Name</div>
  <div class="label" style="left:837px;top:3666px">Last Name</div>
  <div class="input" style="left:579px;top:3694px">Your First Name</div>
  <div class="input" style="left:837px;top:3694px">Your Last Name</div>
  <div class="label" style="left:579px;top:3750px">Email</div>
  <div class="label" style="left:837px;top:3750px">Phone</div>
  <div class="input" style="left:579px;top:3778px">Your Email</div>
  <div class="input" style="left:837px;top:3778px">Your Phone</div>
  <div class="label" style="left:579px;top:3832px">Comment</div>
  <div class="input" style="left:579px;top:3860px;width:509px;height:96px">Enter Your Comment</div>
  <div class="send">SEND MESSAGE</div>
</div>

<!-- footer -->
<svg class="abs footer" width="1200" height="425" viewBox="0 0 1200 425">
  <path d="M0 170 C250 20 750 -20 1200 140 L1200 425 L0 425 Z" fill="#0f1a36"/>
  <path d="M150 120 C420 10 800 0 1200 130" fill="none" stroke="#2a5ea8" stroke-width="18"/>
</svg>
<div class="abs f-logo"><i></i><b>Polarvia</b></div>
<div class="abs f-col" style="left:387px;top:4220px"><h4>NAVIGATION</h4>
  <ul><li>Home</li><li>Cruise Lines</li><li>Destinations</li><li>Itineraries</li><li>Blog/Travel Tips</li><li>About Us</li></ul></div>
<div class="abs f-col" style="left:587px;top:4220px"><h4>QUICK LINKS</h4>
  <ul><li>FAQ</li><li>Contact</li><li>Privacy Policy</li><li>Terms of Use</li></ul></div>
<div class="abs f-col" style="left:776px;top:4220px"><h4>NEWSLETTER</h4></div>
<div class="abs news-line">Email</div>
<div class="abs subscribe">SUBSCRIBE</div>
<div class="abs chat"></div>
<div class="abs f-rule"></div>
<div class="abs copy">2025 © polarvia.co</div>
<div class="abs f-social"><i></i><i></i><i></i><i></i></div>

</body>
</html>
```